Summit Builders Web Site / Business Cards

Construction Company that specializes in Water and Fire Damage, Residential ReModels, Landscaping and Building ADU (Accessory Dwelling Unit)

Growing and changing families often need additional space, and a remodeling project can often provide that. Adding a new area, or repurposing an existing one can satisfy this requirement.

Other times, homeowners want to update the look in their kitchen or bathroom with more than just a change of cabinetry or vanity doors and drawers. Whatever your needs are, Summit Builders has skilled workers who are bonded and insured, and ready to make your dreams and visions a reality.

Target Market(s)

Home Owners

Industry/Entity Type

Construction Company

Contact Information for Business Card

Center Logo with our information on the corners

Back side to be Logo Only
Contact Info
CSLB License # 2418596
info@summitbuildersca.example
www.summitbuildersca.example

Coding

Coded - Design and coding required

Number of Pages Required

5+ page

Font styles to use
Serif
Sans Serif

Requirements
Must have
• Using our Logo Colors
Home
About Us
Services
Projects / Portfolio
Contact Us
Nice to have
• Colors matching our Logo
Should not have
• Black because it doesnt match our logo

```html
<!DOCTYPE html>
<html lang="en">
<head>
<meta charset="utf-8">
<title>Summit Builders</title>
<link href="https://fonts.googleapis.com/css2?family=Open+Sans:wght@400;600;700&family=Roboto:wght@400;500&display=swap" rel="stylesheet">
<style>
:root{
  --orange:#ff6a00;
  --ink:#3b3b3b;
  --body:#5a5a5a;
  --muted:#6b6b6b;
  --tile:#f2f2f2;
  --white:#ffffff;
}
*{box-sizing:border-box;margin:0;padding:0}
html,body{width:1200px;height:3410px;overflow:hidden;background:var(--white)}
body{position:relative;font-family:'Roboto',sans-serif;color:var(--body)}
.abs{position:absolute}
.heading{font-family:'Open Sans',sans-serif;font-weight:700;color:var(--ink);font-size:45px;line-height:1}

/* header */
.site-header{left:0;top:0;width:1200px;height:61px;background:var(--white)}
.brand{left:150px;top:17px;display:flex;align-items:center;gap:8px;font-weight:500;font-size:18px;color:var(--ink)}
.brand .mark{width:14px;height:14px;background:var(--orange)}
.phone{left:927px;top:4px;font-size:13px;color:var(--ink);display:flex;align-items:center;gap:4px}
.nav a{position:absolute;top:35px;font-size:14px;color:var(--ink);text-decoration:none}
.nav .contact{top:33px;left:971px;width:75px;height:20px;background:var(--orange);color:var(--white);text-align:center;line-height:20px}

/* photo areas: tonal fields in the scene colours */
.photo{position:absolute;overflow:hidden}
.hero{left:0;top:61px;width:1200px;height:450px;
  background:
    linear-gradient(90deg,rgba(40,44,52,.55) 0%,rgba(40,44,52,.35) 45%,rgba(40,44,52,.05) 70%,rgba(20,24,36,.25) 100%),
    radial-gradient(ellipse 150px 230px at 640px 300px,#e0902a 0%,rgba(224,144,42,0) 100%),
    radial-gradient(ellipse 170px 260px at 860px 250px,#f0a030 0%,rgba(240,160,48,0) 100%),
    radial-gradient(ellipse 160px 300px at 1080px 300px,#2b3148 0%,rgba(43,49,72,0) 100%),
    linear-gradient(180deg,#7a7f86 0%,#6a6f74 55%,#8c8378 100%)}
.hero-title{left:150px;top:120px;font-family:'Open Sans',sans-serif;font-weight:700;font-size:50px;line-height:53px;color:var(--white)}
.hero-text{left:150px;top:246px;width:385px;font-size:15.5px;line-height:22.5px;color:var(--white)}
.btn{background:var(--orange);color:var(--white);display:flex;align-items:center;justify-content:center;text-decoration:none}
.quote-btn{left:150px;top:368px;width:200px;height:45px;font-size:15px;font-weight:500;border-radius:2px}

/* feature band */
.features{left:0;top:511px;width:1200px;height:77px;background:var(--orange)}
.feature{position:absolute;top:0;height:77px;display:flex;align-items:center;color:var(--white);font-size:13px;line-height:20px;font-weight:500}
.feature svg{position:absolute;top:16px}

/* services */
.services-photo{left:0;top:657px;width:429px;height:522px;
  background:
    radial-gradient(ellipse 70px 55px at 250px 75px,#f4f4f2 0%,rgba(244,244,242,0) 100%),
    radial-gradient(ellipse 70px 80px at 250px 175px,#d79a78 0%,rgba(215,154,120,0) 100%),
    radial-gradient(ellipse 170px 220px at 250px 420px,#3e5d9a 0%,rgba(62,93,154,0) 100%),
    radial-gradient(ellipse 170px 170px at 90px 450px,#eceae6 0%,rgba(236,234,230,0) 100%),
    linear-gradient(180deg,#cfdceb 0%,#bccfe4 60%,#d6dde6 100%)}
.services-title{left:478px;top:650px}
.service{position:absolute;width:160px}
.service .tile{width:89px;height:89px;background:var(--tile);display:flex;align-items:center;justify-content:center}
.service h3{margin-top:23px;font-size:14.5px;font-weight:500;color:var(--ink)}
.service p{margin-top:9px;width:155px;font-size:11.5px;line-height:20px;color:var(--muted)}

/* projects */
.projects-title{left:0;width:1200px;top:1243px;text-align:center}
.house{left:0;top:1334px;width:724px;height:339px;
  background:
    linear-gradient(180deg,#dfe8ef 0%,#dfe8ef 8%,#c9464a 14%,#d65a5a 30%,#e8eaec 36%,#f3f4f5 60%,#dfe3e8 78%,#6f8c45 88%,#4d6a2e 100%)}
.project-panel{left:732px;top:1334px;width:468px;height:339px;
  background:
    linear-gradient(180deg,rgba(96,94,94,.88),rgba(90,88,88,.88)),
    linear-gradient(180deg,#d8d8d6 0%,#bfc3c2 55%,#6fa6a8 75%,#cfcac2 100%)}
.project-panel h3{position:absolute;left:38px;top:50px;font-family:'Open Sans',sans-serif;font-weight:400;font-size:31px;color:var(--white)}
.project-panel p{position:absolute;left:39px;top:104px;width:268px;font-size:14.5px;line-height:20px;color:var(--white)}
.read-more{position:absolute;left:39px;top:225px;width:159px;height:41px;background:var(--white);color:var(--ink);font-size:18px;display:flex;align-items:center;justify-content:center;text-decoration:none}
.kitchen{left:0;top:1682px;width:468px;height:338px;
  background:
    radial-gradient(ellipse 50px 150px at 55px 200px,#8f9295 0%,rgba(143,146,149,0) 100%),
    linear-gradient(180deg,#f4f4f4 0%,#ececec 36%,#3d3f42 42%,#4a4c4f 52%,#d8d8d8 58%,#e9e9e9 72%,#5e4a3c 82%,#4a3a30 100%)}
.villa{left:475px;top:1682px;width:725px;height:338px;
  background:
    linear-gradient(180deg,#7fa4c8 0%,#a9c1d8 22%,#e8ddd2 32%,#c99a78 44%,#e6dcd2 52%,#2f3438 60%,#3b4247 74%,#5fc4cc 82%,#49b3bd 90%,#e9e9e7 100%)}

/* about */
.about-title{left:150px;top:2095px}
.about-text{left:150px;width:500px;font-size:15.5px;line-height:22.5px;color:var(--body)}
.know-btn{left:150px;top:2526px;width:239px;height:54px;font-size:18px}
.about-photo{left:685px;top:2099px;width:515px;height:522px;
  background:
    radial-gradient(ellipse 200px 120px at 240px 210px,#d7b39a 0%,rgba(215,179,154,0) 100%),
    radial-gradient(ellipse 160px 130px at 160px 330px,#e6eaf2 0%,rgba(230,234,242,0) 100%),
    radial-gradient(ellipse 120px 160px at 440px 200px,#f1f1f1 0%,rgba(241,241,241,0) 100%),
    linear-gradient(180deg,#8b8a86 0%,#b7b3ad 30%,#cfcac3 58%,#c9a577 74%,#b48b5c 100%)}

/* stats */
.stats{left:0;top:2697px;width:1200px;height:94px;background:var(--orange)}
.stat{position:absolute;top:18px;width:180px;text-align:center;color:var(--white)}
.stat strong{display:block;font-size:29px;font-weight:500;line-height:32px}
.stat span{display:block;margin-top:4px;font-size:14px}

/* testimonials */
.testi-title{left:0;width:1200px;top:2843px;text-align:center}
.card{position:absolute;top:2930px;width:265px;height:357px;background:var(--white);box-shadow:0 2px 10px rgba(60,60,60,.12)}
.avatar{position:absolute;left:10px;top:18px;width:95px;height:95px;border-radius:50%}
.card p{position:absolute;left:10px;top:147px;width:248px;font-family:'Open Sans',sans-serif;font-size:13.6px;line-height:20px;color:var(--ink)}
.arrow{position:absolute;top:3305px;width:52px;height:52px}
</style>
</head>
<body>

<header class="abs site-header">
  <div class="abs brand"><span class="mark"></span>Summit Builders</div>
  <div class="abs phone">
    <svg width="14" height="14" viewBox="0 0 24 24"><path fill="#ff6a00" d="M6.6 10.8a15 15 0 0 0 6.6 6.6l2.2-2.2c.3-.3.7-.4 1-.2 1.1.4 2.3.6 3.6.6.6 0 1 .4 1 1V20c0 .6-.4 1-1 1A17 17 0 0 1 3 4c0-.6.4-1 1-1h3.5c.6 0 1 .4 1 1 0 1.3.2 2.5.6 3.6.1.3 0 .7-.2 1z"/></svg>
    +1 555 014 2273
  </div>
  <nav class="nav">
    <a style="left:651px">Home</a>
    <a style="left:719px">Company</a>
    <a style="left:809px">Projects</a>
    <a style="left:889px">Services</a>
    <a class="contact">Contact</a>
  </nav>
</header>

<section class="photo hero" role="img" aria-label="Two engineers in hard hats and orange safety vests reviewing plans at a building site"></section>
<h1 class="abs hero-title">The best choose us<br>Because we deliver</h1>
<p class="abs hero-text">Lorem ipsum dolor sit amet, consectetur adipisicing elit, sed do eiusmod tempor incididunt ut labore et dolore magna aliqua. Ut enim ad minim veniam, quis</p>
<a class="abs btn quote-btn">Get a Quote</a>

<section class="abs features">
  <div class="feature" style="left:150px;width:220px">
    <svg style="left:0" width="48" height="48" viewBox="0 0 48 48"><path d="M24 4l6 13 14 1.5-10.5 9.5 3 14L24 35l-12.5 7 3-14L4 18.5 18 17z" fill="none" stroke="#fff" stroke-width="2.5" stroke-linejoin="round"/></svg>
    <span style="margin-left:68px">We've Reputation<br>for excellence</span>
  </div>
  <div class="feature" style="left:397px;width:220px">
    <svg style="left:0" width="80" height="48" viewBox="0 0 80 48"><path d="M3 10h10v26H3zM67 10h10v26H67zM13 14l14-5 14 6 12-6 14 5M13 32l8 0 8 6 6 0 8-6 6 0 6-4 0-12M27 22l8 6 6-6 8 6" fill="none" stroke="#fff" stroke-width="2.5" stroke-linejoin="round"/></svg>
    <span style="margin-left:100px">We build<br>Partnerships</span>
  </div>
  <div class="feature" style="left:642px;width:220px">
    <svg style="left:0;top:6px" width="52" height="58" viewBox="0 0 52 58"><path d="M3 26h10v28H3zM13 28l10-14V4c6 0 8 5 7 14h16c3 0 5 3 4 6l-5 24c-1 4-3 6-7 6H13" fill="none" stroke="#fff" stroke-width="2.5" stroke-linejoin="round"/><path d="M36 8l4-5M42 12l6-2M38 4V0" stroke="#fff" stroke-width="2.5"/></svg>
    <span style="margin-left:69px">Guided by<br>Commitment</span>
  </div>
  <div class="feature" style="left:890px;width:220px">
    <svg style="left:0" width="58" height="48" viewBox="0 0 58 48"><circle cx="29" cy="11" r="7" fill="none" stroke="#fff" stroke-width="2.5"/><circle cx="11" cy="17" r="6" fill="none" stroke="#fff" stroke-width="2.5"/><circle cx="47" cy="17" r="6" fill="none" stroke="#fff" stroke-width="2.5"/><path d="M17 46V30c0-6 5-10 12-10s12 4 12 10v16M2 46V34c0-5 4-8 9-8s6 1 6 1M56 46V34c0-5-4-8-9-8s-6 1-6 1" fill="none" stroke="#fff" stroke-width="2.5"/></svg>
    <span style="margin-left:78px">A team of<br>Professionals</span>
  </div>
</section>

<div class="photo services-photo" role="img" aria-label="Builder in a white hard hat and blue checked shirt holding rolled blueprints"></div>
<h2 class="abs heading services-title">Services We Provide</h2>

<div class="service" style="left:481px;top:738px">
  <div class="tile"><svg width="42" height="42" viewBox="0 0 24 24"><path fill="#ff6a00" d="M12 2L1 12h3v9h6v-6h4v6h6v-9h3z"/></svg></div>
  <h3>Home Construction</h3><p>Lorem ipsum dolor sit amet, consectetur adipisicing elit, sed do eiusmod tempor</p>
</div>
<div class="service" style="left:689px;top:738px">
  <div class="tile"><svg width="42" height="42" viewBox="0 0 24 24"><path fill="#ff6a00" d="M3 2h6v13h12v7H3z"/><path d="M12 15v3M15 15v2M18 15v3M9 5H6M9 8H7M9 11H6" stroke="#f2f2f2" stroke-width="1.2"/></svg></div>
  <h3>Home Construction</h3><p>Lorem ipsum dolor sit amet, consectetur adipisicing elit, sed do eiusmod tempor</p>
</div>
<div class="service" style="left:901px;top:738px">
  <div class="tile"><svg width="42" height="42" viewBox="0 0 24 24"><path fill="#ff6a00" d="M5 2h13v6H5zM18 4h2v7h-8v3h-2V9h8V4zM9.5 14h3v8h-3z"/></svg></div>
  <h3>Home Construction</h3><p>Lorem ipsum dolor sit amet, consectetur adipisicing elit, sed do eiusmod tempor</p>
</div>
<div class="service" style="left:481px;top:995px">
  <div class="tile"><svg width="42" height="42" viewBox="0 0 24 24"><path d="M4 4l16 16M20 4L8 16" stroke="#ff6a00" stroke-width="3" stroke-linecap="round"/><circle cx="18" cy="6" r="3" fill="#ff6a00"/><circle cx="6" cy="18" r="3" fill="#ff6a00"/></svg></div>
  <h3>Home Construction</h3><p>Lorem ipsum dolor sit amet, consectetur adipisicing elit, sed do eiusmod tempor</p>
</div>
<div class="service" style="left:686px;top:995px">
  <div class="tile"><svg width="42" height="42" viewBox="0 0 24 24"><path fill="#ff6a00" d="M14 2l8 8-6 4-6-6zM9 9l6 6-3 2-5-5zM7 13l4 4-6 6-4-4z"/></svg></div>
  <h3>Home Construction</h3><p>Lorem ipsum dolor sit amet, consectetur adipisicing elit, sed do eiusmod tempor</p>
</div>
<div class="service" style="left:901px;top:995px">
  <div class="tile"><svg width="42" height="42" viewBox="0 0 24 24"><path fill="#ff6a00" d="M2 18h20v3H2zM4 17a8 8 0 0 1 5-7v7zM10 6h4v11h-4zM15 10a8 8 0 0 1 5 7h-5z"/></svg></div>
  <h3>Home Construction</h3><p>Lorem ipsum dolor sit amet, consectetur adipisicing elit, sed do eiusmod tempor</p>
</div>

<h2 class="abs heading projects-title">Recent Projects</h2>
<div class="photo house" role="img" aria-label="White two-storey house with a red metal roof and flower baskets"></div>
<div class="abs project-panel" role="group" aria-label="Featured project over a kitchen interior photo">
  <h3>Lorem Ipsum</h3>
  <p>Lorem ipsum dolor sit amet, consectetur adipisicing elit, sed do eiusmod tempor incididunt ut labore et dolore magna aliqua. Ut enim ad minim veniam, quis</p>
  <a class="read-more">Read More</a>
</div>
<div class="photo kitchen" role="img" aria-label="Modern white kitchen with steel appliances, pendant lamps and bar stools"></div>
<div class="photo villa" role="img" aria-label="Contemporary villa with large glass windows and a turquoise pool"></div>

<h2 class="abs heading about-title">Who we are</h2>
<p class="abs about-text" style="top:2183px">Lorem ipsum dolor sit amet, consectetur adipisicing elit, sed do eiusmod tempor incididunt ut labore et dolore magna aliqua. Ut enim ad minim veniam, quis nostrud exercitation ullamco laboris nisi ut aliquip ex ea</p>
<p class="abs about-text" style="top:2294px">Lorem ipsum dolor sit amet, consectetur adipisicing elit, sed do eiusmod tempor incididunt ut labore et dolore magna aliqua. Ut enim ad minim veniam, quis nostrud exercitation ullamco laboris nisi ut aliquip ex ea</p>
<p class="abs about-text" style="top:2405px">Lorem ipsum dolor sit amet, consectetur adipisicing elit, sed do eiusmod tempor incididunt ut labore et dolore magna aliqua. Ut enim ad minim veniam, quis nostrud exercitation ullamco laboris nisi ut aliquip ex ea</p>
<a class="abs btn know-btn">Know More</a>
<div class="photo about-photo" role="img" aria-label="Team of colleagues joining hands over a wooden table with a laptop"></div>

<section class="abs stats">
  <div class="stat" style="left:245px"><strong>53</strong><span>Total Projects</span></div>
  <div class="stat" style="left:424px"><strong>371</strong><span>Staff Members</span></div>
  <div class="stat" style="left:607px"><strong>15</strong><span>Working in states</span></div>
  <div class="stat" style="left:774px"><strong>2,600</strong><span>Hours for work</span></div>
</section>

<h2 class="abs heading testi-title">Testimonial</h2>
<div class="card" style="left:150px">
  <div class="avatar" style="background:radial-gradient(circle at 50% 40%,#c9d2db,#4c5a70)" role="img" aria-label="Client portrait"></div>
  <p>Lorem ipsum dolor sit amet, consectetur adipisicing elit, sed do eiusmod tempor incididunt ut labore et dolore magna aliqua. Ut enim ad minim veniam, quis nostrud exercitation ullamco laboris nisi ut aliquip ex ea commodo consequat. Duis aute irure dolor in reprehenderit in voluptate velit esse cillum dolore eu</p>
</div>
<div class="card" style="left:465px">
  <div class="avatar" style="background:radial-gradient(circle at 50% 40%,#e2e2e2,#8a8f96)" role="img" aria-label="Client portrait"></div>
  <p>Lorem ipsum dolor sit amet, consectetur adipisicing elit, sed do eiusmod tempor incididunt ut labore et dolore magna aliqua. Ut enim ad minim veniam, quis nostrud exercitation ullamco laboris nisi ut aliquip ex ea commodo consequat. Duis aute irure dolor in reprehenderit in voluptate velit esse cillum dolore eu</p>
</div>
<div class="card" style="left:780px">
  <div class="avatar" style="background:radial-gradient(circle at 50% 45%,#8a5e44,#2e2420 70%,#f2f2f2 100%)" role="img" aria-label="Client portrait"></div>
  <p>Lorem ipsum dolor sit amet, consectetur adipisicing elit, sed do eiusmod tempor incididunt ut labore et dolore magna aliqua. Ut enim ad minim veniam, quis nostrud exercitation ullamco laboris nisi ut aliquip ex ea commodo consequat. Duis aute irure dolor in reprehenderit in voluptate velit esse cillum dolore eu</p>
</div>

<svg class="arrow" style="left:514px" viewBox="0 0 52 52"><circle cx="26" cy="26" r="24.5" fill="none" stroke="#ff6a00" stroke-width="2"/><path d="M30 16L20 26l10 10" fill="none" stroke="#ff6a00" stroke-width="2"/></svg>
<svg class="arrow" style="left:634px" viewBox="0 0 52 52"><circle cx="26" cy="26" r="24.5" fill="none" stroke="#ff6a00" stroke-width="2"/><path d="M22 16l10 10-10 10" fill="none" stroke="#ff6a00" stroke-width="2"/></svg>

</body>
</html>
```